Using attached logo that has been created

Business card with logo that's attached. Maybe with water or the cartoon van in background. Looking for it to not be so plain and not too white.
Information to include;
Rodney Ashcombe
(555) 218-7730
Info@bramleypipeworks.example
www.bramleypipeworks.example
License # 4627195
Looking forward to the designs u come up with.
Thank you!
-Delphine
Target Market(s)
Plumbing
Industry/Entity Type
Plumbing
Contact Information for Business Card
Listed above

```html
<!DOCTYPE html>
<html lang="en">
<head>
<meta charset="utf-8">
<title>Bramley Pipeworks – Business Card</title>
<link href="https://fonts.googleapis.com/css2?family=Poppins:wght@400;500;600;700&display=swap" rel="stylesheet">
<style>
  :root {
    --page-bg: #d9dadb;
    --brand-blue: #1763b8;
    --brand-blue-light: #2f8bdc;
    --brand-blue-deep: #1a5bb0;
    --brand-yellow: #f5b800;
    --card-white: #f6f7f8;
    --card-grey: #e6e8ea;
    --ink: #222427;
    --white: #ffffff;
  }
  * { box-sizing: border-box; margin: 0; padding: 0; }
  html, body {
    width: 1187px; height: 1200px; overflow: hidden;
    background: var(--page-bg);
    font-family: "Poppins", sans-serif;
  }
  .canvas { position: relative; width: 1187px; height: 1200px; }

  .card {
    position: absolute; left: 215px; width: 757px; height: 432px;
    border-radius: 14px; overflow: hidden;
  }
  .card--front {
    top: 122px;
    background: radial-gradient(ellipse at 50% 40%, var(--brand-blue-light) 0%, var(--brand-blue) 75%, #1658a6 100%);
  }
  .card--back {
    top: 644px;
    background: radial-gradient(ellipse at 40% 50%, var(--card-white) 0%, var(--card-grey) 100%);
  }

  .mascot {
    position: absolute; border-radius: 10px;
  }
  .card--front .mascot {
    left: 313px; top: 46px; width: 170px; height: 250px;
    background: linear-gradient(180deg, #2a6fc4 0%, #3a78c0 50%, #8a7658 100%);
  }
  .card--back .mascot {
    left: 150px; top: 70px; width: 165px; height: 215px;
    background: linear-gradient(180deg, #3a6fb8 0%, #4a7cc0 50%, #8f7a5a 100%);
  }

  .brand-name {
    position: absolute; font-weight: 700; white-space: nowrap;
    letter-spacing: 0.5px; text-transform: uppercase;
  }
  .card--front .brand-name {
    left: 0; right: 0; top: 300px; text-align: center;
    font-size: 30px; color: var(--white);
  }
  .card--back .brand-name {
    left: 72px; width: 320px; top: 292px; text-align: center;
    font-size: 24px; color: var(--brand-blue-deep);
  }

  .divider-vertical {
    position: absolute; left: 380px; top: 125px; width: 2px; height: 186px;
    background: var(--brand-yellow);
  }
  .person-name {
    position: absolute; left: 410px; top: 126px;
    font-size: 27px; font-weight: 700; color: var(--brand-blue-deep);
    letter-spacing: 0.3px; text-transform: uppercase;
  }
  .person-title {
    position: absolute; left: 411px; top: 163px;
    font-size: 15px; font-weight: 500; color: var(--ink); letter-spacing: 0.5px;
  }
  .divider-horizontal {
    position: absolute; left: 410px; top: 192px; width: 236px; height: 1.5px;
    background: var(--brand-yellow);
  }
  .contact-list { list-style: none; }
  .contact-item {
    position: absolute; left: 411px; display: flex; align-items: center; gap: 8px;
    font-size: 17px; color: var(--ink); letter-spacing: 0.6px; white-space: nowrap;
  }
  .contact-item--phone { top: 207px; }
  .contact-item--email { top: 243px; }
  .contact-item--web { top: 284px; }
  .contact-icon { width: 20px; height: 20px; flex: none; }

  .license-band {
    position: absolute; left: 0; right: 0; top: 369px; height: 37px;
    background: var(--brand-blue);
    border-top: 3px solid var(--brand-yellow);
    border-bottom: 3px solid var(--brand-yellow);
    display: flex; align-items: center; justify-content: center;
    color: var(--white); font-weight: 600; font-size: 17px; letter-spacing: 0.8px;
  }
</style>
</head>
<body>
<main class="canvas">

  <section class="card card--front" aria-label="Business card front">
    <div class="mascot" role="img" aria-label="Cartoon plumber mascot holding a pipe wrench and a circular saw"></div>
    <div class="brand-name">Bramley Pipeworks</div>
  </section>

  <section class="card card--back" aria-label="Business card back">
    <div class="mascot" role="img" aria-label="Cartoon plumber mascot holding a pipe wrench and a circular saw"></div>
    <div class="brand-name">Bramley Pipeworks</div>

    <div class="divider-vertical"></div>
    <h1 class="person-name">Rodney Ashcombe</h1>
    <p class="person-title">OWNER</p>
    <div class="divider-horizontal"></div>

    <ul class="contact-list">
      <li class="contact-item contact-item--phone">
        <svg class="contact-icon" viewBox="0 0 20 20" aria-hidden="true">
          <circle cx="10" cy="10" r="10" fill="var(--brand-blue)"/>
          <path d="M6.6 5.2l1.7-.3 1 2.4-1.1.9a6 6 0 0 0 2.8 2.8l.9-1.1 2.4 1-.3 1.7c-.1.5-.6.9-1.1.8A8.4 8.4 0 0 1 5.8 6.3c-.1-.5.3-1 .8-1.1z" fill="var(--white)"/>
        </svg>
        <span>(555) 218-7730</span>
      </li>
      <li class="contact-item contact-item--email">
        <svg class="contact-icon" viewBox="0 0 20 20" aria-hidden="true">
          <circle cx="10" cy="10" r="10" fill="var(--brand-blue)"/>
          <rect x="5" y="6.5" width="10" height="7" rx="1" fill="var(--white)"/>
          <path d="M5.3 7l4.7 3.6L14.7 7" fill="none" stroke="var(--brand-blue)" stroke-width="1"/>
        </svg>
        <span>Info@bramleypipeworks.example</span>
      </li>
      <li class="contact-item contact-item--web">
        <svg class="contact-icon" viewBox="0 0 20 20" aria-hidden="true">
          <circle cx="10" cy="10" r="10" fill="var(--brand-blue)"/>
          <g fill="none" stroke="var(--white)" stroke-width="0.9">
            <circle cx="10" cy="10" r="5"/>
            <ellipse cx="10" cy="10" rx="2.2" ry="5"/>
            <path d="M5 10h10M5.8 7.5h8.4M5.8 12.5h8.4"/>
          </g>
        </svg>
        <span>www.bramleypipeworks.example</span>
      </li>
    </ul>

    <div class="license-band">License # 4627195</div>
  </section>

</main>
</body>
</html>
```